Business card for my new company (Accounting firm)

I need a business card for my new business Brightwell Advisory and Ledger SA. Our services are accounting, tax, audit and financial management. Our customers are small companies, start-ups and new companies. The final design has to show financial security, trust and growth. Please find our logo attached to the business card. Text for the business card: Brightwell Advisory and Ledger SA Tomas Varenholt Director and Founder Certified Accountant Tel. 022 418 57 34 tv@clairevalconseil.ch www.clairevalconseil.ch Rue des Vergières 27 1201 Geneva
Target Market(s)
Our customers are small companies, start-ups and new companies.
Industry/Entity Type
Finance And Accounting
Contact Information for Business Card
Claireval Conseil et Comptes SA
Tomas Varenholt
Directeur et Fondateur
Expert-comptable diplômé
Tél. 022 418 57 34
tv@clairevalconseil.ch
www.clairevalconseil.ch
Rue des Vergières 27
1201 Genève

```html
<!DOCTYPE html>
<html lang="fr">
<head>
<meta charset="utf-8">
<title>Claireval Conseil et Comptes SA – Carte de visite</title>
<link rel="stylesheet" href="https://fonts.googleapis.com/css2?family=Roboto:wght@400;500;700&display=swap">
<style>
  :root {
    --backdrop: #e6e8eb;
    --brand-blue: #1b6497;
    --accent-blue: #2fa7dc;
    --ink: #3a3a3a;
    --ink-soft: #5c5c5c;
    --swoosh: #3d3d3d;
    --paper: #ffffff;
  }
  * { box-sizing: border-box; margin: 0; padding: 0; }
  html, body { width: 1200px; height: 960px; overflow: hidden; }
  body {
    background: var(--backdrop);
    font-family: "Roboto", Arial, sans-serif;
    display: flex;
    flex-direction: column;
    align-items: center;
    justify-content: center;
    gap: 40px;
  }
  .card {
    position: relative;
    width: 720px;
    height: 412px;
    overflow: hidden;
    box-shadow: 0 6px 18px rgba(0,0,0,0.18);
  }

  /* Back side */
  .card-back { background: var(--brand-blue); }
  .card-back .pattern-field {
    position: absolute; inset: 0;
    background: linear-gradient(135deg, #1d6a9f 0%, #1a5f90 100%);
  }
  .card-back .back-name {
    position: absolute;
    right: 70px;
    top: 212px;
    color: var(--paper);
    font-weight: 700;
    font-size: 24px;
    letter-spacing: 0.5px;
  }

  /* Front side */
  .card-front { background: var(--paper); }
  .card-front .shapes { position: absolute; inset: 0; }
  .brand {
    position: absolute;
    left: 48px;
    top: 70px;
    display: flex;
    align-items: center;
    gap: 12px;
  }
  .brand-dot {
    width: 30px; height: 30px;
    border-radius: 50%;
    background: var(--accent-blue);
  }
  .brand-name {
    font-weight: 700;
    font-size: 44px;
    color: var(--ink);
    letter-spacing: 1px;
  }
  .address {
    position: absolute;
    left: 52px;
    top: 186px;
    font-size: 17px;
    line-height: 1.35;
    color: var(--ink-soft);
  }
  .contact-list {
    position: absolute;
    left: 52px;
    top: 262px;
    list-style: none;
    font-size: 17px;
    color: var(--ink-soft);
  }
  .contact-list li {
    display: flex;
    align-items: center;
    gap: 10px;
    line-height: 1.55;
  }
  .contact-list svg { width: 15px; height: 15px; flex: none; }
  .person {
    position: absolute;
    right: 24px;
    bottom: 40px;
    text-align: right;
    color: var(--paper);
  }
  .person-name { font-weight: 700; font-size: 23px; line-height: 1.25; }
  .person-role { font-size: 15px; line-height: 1.35; }
</style>
</head>
<body>

  <section class="card card-back" aria-label="Verso de la carte">
    <div class="pattern-field" role="img" aria-label="Motif répété du symbole de la marque en bleu clair sur fond bleu"></div>
    <span class="back-name">Claireval</span>
  </section>

  <section class="card card-front" aria-label="Recto de la carte">
    <svg class="shapes" viewBox="0 0 720 412" preserveAspectRatio="none" aria-hidden="true">
      <path d="M600 0 C680 110 560 330 300 412 L720 412 L720 0 Z" fill="var(--brand-blue)"/>
      <path d="M560 24 C620 120 530 330 250 412 L285 412 C565 320 640 130 560 24 Z" fill="var(--swoosh)"/>
    </svg>

    <div class="brand">
      <span class="brand-dot"></span>
      <span class="brand-name">Claireval</span>
    </div>

    <p class="address">Rue des Vergières 27<br>1201 Genève</p>

    <ul class="contact-list">
      <li>
        <svg viewBox="0 0 24 24"><path fill="var(--accent-blue)" d="M6.6 10.8a15 15 0 0 0 6.6 6.6l2.2-2.2c.3-.3.7-.4 1-.2 1.1.4 2.3.6 3.6.6.6 0 1 .4 1 1V20c0 .6-.4 1-1 1A17 17 0 0 1 3 4c0-.6.4-1 1-1h3.5c.6 0 1 .4 1 1 0 1.3.2 2.5.6 3.6.1.3 0 .7-.2 1z"/></svg>
        022 418 57 34
      </li>
      <li>
        <svg viewBox="0 0 24 24"><path fill="var(--accent-blue)" d="M2 5h20v14H2z"/><path d="M2 5l10 8 10-8" fill="none" stroke="#fff" stroke-width="2"/></svg>
        tv@clairevalconseil.ch
      </li>
      <li>
        <svg viewBox="0 0 24 24"><circle cx="12" cy="12" r="10" fill="var(--accent-blue)"/><path d="M2 12h20M12 2c3 3 3 17 0 20M12 2c-3 3-3 17 0 20" fill="none" stroke="#fff" stroke-width="1.5"/></svg>
        www.clairevalconseil.ch
      </li>
    </ul>

    <div class="person">
      <p class="person-name">Tomas Varenholt</p>
      <p class="person-role">Directeur et Fondateur</p>
      <p class="person-role">Expert-comptable diplômé</p>
    </div>
  </section>

</body>
</html>
```